Business Card Design

We need a business card designed for our new company. Prefer a black card with white logo & writing.

Contact Information for Business Card

Ted Galloway, address: 7-4812 Fernhollow Road, Abbotsford, BC, V3K 8R2, Office Phone: 604-712-3390, Cell: 604-947-2164, Email: ted@resinworkshub.ca

Colors

Designer to choose only greyscale colors for use in the design.

```html
<!DOCTYPE html>
<html lang="en">
<head>
<meta charset="utf-8">
<title>Resin Works Hub — Business Card</title>
<link rel="stylesheet" href="https://fonts.googleapis.com/css2?family=Montserrat:wght@400;700&display=swap">
<style>
  :root {
    --backdrop: #9b9b9b;
    --card: #212121;
    --ink: #ffffff;
    --ink-soft: #e6e6e6;
    --emboss: #101010;
  }
  * { margin: 0; padding: 0; box-sizing: border-box; }
  html, body {
    width: 1093px; height: 1200px; overflow: hidden;
    background: var(--backdrop);
    font-family: "Montserrat", sans-serif;
  }
  .canvas { position: relative; width: 1093px; height: 1200px; }
  .card {
    position: absolute; left: 265px; width: 582px; height: 364px;
    background: var(--card); border-radius: 17px; overflow: hidden;
  }
  .card--front { top: 225px; }
  .card--back { top: 616px; }

  .holder { position: absolute; left: 29px; top: 38px; color: var(--ink); }
  .holder__name { font-weight: 700; font-size: 21px; letter-spacing: 0.2px; line-height: 1.2; }
  .holder__role { font-weight: 400; font-size: 13px; color: var(--ink-soft); margin-top: 2px; }

  .brand {
    position: absolute; left: 370px; top: 52px; width: 150px;
    display: flex; flex-direction: column; align-items: center; gap: 8px;
    color: var(--ink); font-weight: 700; text-align: center;
  }
  .brand__mark { width: 18px; height: 18px; background: var(--ink); }
  .brand__name { font-size: 20px; line-height: 1.1; letter-spacing: 0.5px; }

  .contacts {
    position: absolute; left: 27px; top: 254px; list-style: none;
    color: var(--ink-soft); font-size: 13.2px;
  }
  .contacts li { display: flex; align-items: center; gap: 9px; height: 22px; }
  .contacts svg { width: 14px; height: 14px; fill: var(--ink); flex: none; }

  .address {
    position: absolute; left: 369px; top: 305px;
    color: var(--ink-soft); font-size: 13.2px; line-height: 16px; font-style: normal;
  }

  .brand-large {
    position: absolute; inset: 0;
    display: flex; align-items: center; justify-content: center;
    color: var(--emboss); font-weight: 700; font-size: 54px;
    text-align: center; line-height: 1.05; letter-spacing: 1px;
  }
</style>
</head>
<body>
<main class="canvas">
  <section class="card card--front">
    <div class="holder">
      <p class="holder__name">Ted Galloway</p>
      <p class="holder__role">owner</p>
    </div>

    <div class="brand">
      <span class="brand__mark"></span>
      <span class="brand__name">RESIN WORKS HUB</span>
    </div>

    <ul class="contacts">
      <li>
        <svg viewBox="0 0 24 24" aria-hidden="true"><path d="M6.6 10.8a15.1 15.1 0 0 0 6.6 6.6l2.2-2.2c.3-.3.7-.4 1-.2 1.1.4 2.3.6 3.6.6.6 0 1 .4 1 1V20c0 .6-.4 1-1 1A17 17 0 0 1 3 4c0-.6.4-1 1-1h3.5c.6 0 1 .4 1 1 0 1.3.2 2.5.6 3.6.1.3 0 .7-.2 1z"/></svg>
        604-712-3390
      </li>
      <li>
        <svg viewBox="0 0 24 24" aria-hidden="true"><path d="M7 1h10a2 2 0 0 1 2 2v18a2 2 0 0 1-2 2H7a2 2 0 0 1-2-2V3a2 2 0 0 1 2-2zm0 3v14h10V4zm5 15.2a1.2 1.2 0 1 0 0 2.4 1.2 1.2 0 0 0 0-2.4z"/></svg>
        604-947-2164
      </li>
      <li>
        <svg viewBox="0 0 24 24" aria-hidden="true"><path d="M2 5h20v2l-10 6L2 7zm0 4.3 10 6 10-6V19H2z"/></svg>
        ted@resinworkshub.ca
      </li>
      <li>
        <svg viewBox="0 0 24 24" aria-hidden="true"><path d="M12 2a10 10 0 1 0 0 20 10 10 0 0 0 0-20zm-1 17.9A8 8 0 0 1 4.2 10.2L9 15v1a2 2 0 0 0 2 2zm6.9-2.5A2 2 0 0 0 16 16h-1v-3a1 1 0 0 0-1-1H8v-2h2a1 1 0 0 0 1-1V7h2a2 2 0 0 0 2-2v-.4a8 8 0 0 1 2.9 12.8z"/></svg>
        www.resinworkshub.ca
      </li>
    </ul>

    <address class="address">
      7-4812 Fernhollow Road,<br>
      Abbotsford, BC, V3K 8R2
    </address>
  </section>

  <section class="card card--back">
    <div class="brand-large">RESIN WORKS<br>HUB</div>
  </section>
</main>
</body>
</html>
```